Redesign company trifold brochure

We are rebranding our company in September and looking for a more professional design for our brochure.

What we do - providing interdisciplinary care for those supporting ill, elderly and special needs pets at home following the human hospice model of care - is very novel and our brochure is key in explaining it and our offerings.

We serve dogs and cats. Most of the animals are quite sick, elderly. I have many personal and stock photos we can use in the brochure. Please - no pictures of puppies and/or kittens.

The hard part is fitting the info and message into a clear and concise format.

It must be appealing both to pet owners and vets (who are our primary source of patients through referrals).

It should covey WARMTH, COMPASSION, PROFESSIONALISM, and EXPERTISE.

Please look at our website www.TrellisAnimalRespite.com for more info

We have until now used maroon and copper for colors - to reflect the "sunset" of the pets life. BUT are now changing to Navy, Teal and White to reflect calm, trust and competence.

We will use the same logo recolored.

Existing brochure and new logo are attached.

PLEASE ask questions!!
Updates

We have a library of stock images you are welcome to use. All have been legally acquired and we have the right to use them. You DO NOT have to use them, just sending along in case you wish to. https://www.filecrate.example/sh/qk4vrm82zd1pyno/KLQ7Ztbn-Rrfx2mh9sWpYJ4Dc?dl=0

Our colors are NAVY, TEAL and WHITE. For your reference, the navy we use is 99/87/44/55 (CMYK) The Teal we use is 76/11/44/0 (CMYK) Thank you!

Designers -- pleaseuse pictures of older pets (no puppies or kittens). Below is a link to stock photos we own that would be appropriate for use in the brochure. https://www.filecrate.example/sh/w274m6t9pxkr5da/KLRn3GsfwlTVBXEPcq_8ZNj5u?dl=0 THANK YOU!

Designers -- I would VERY much like to include a photo of a pet in a wheel chair. I have personal photos as well as (purchased) stock photos for this purpose which can be found at http://lnk.example/TARHC-Pets-in-Wheelchairs Thank you!!

Today is the last day! Many of you have submitted beautiful designs and others are rolling in. I am so appreciative of your time and energy!! Please do not let the deadline pass without YOUR very BEST entry being submitted!! Thank you! - Miriam & All of us at Trellis Animal Respite & Home Care

Target Market(s)

Pet Owners and Veterinarians

Industry/Entity Type

Pet Care

Font styles to use
Serif

Colors
0455a3
33b8a4
ffffff

Requirements
Must have
• Our logo and information about our services. Pictures of pets. Our contact info. PLEASE NOTE: this is a 2 sided brochure. Please submit both inside and outside.
Should not have
• puppies, kittens - anything off message

```html
<!DOCTYPE html>
<html lang="en">
<head>
<meta charset="utf-8">
<title>Trellis Animal Respite &amp; Home Care – Trifold Brochure</title>
<link rel="stylesheet" href="https://fonts.googleapis.com/css2?family=Cormorant+Garamond:ital,wght@1,500;1,600&family=Open+Sans:ital,wght@0,400;0,600;1,400&display=swap">
<style>
  :root {
    --bg: #e4e5e7;
    --navy: #0b2152;
    --teal: #33b8a4;
    --teal-soft: #6cc4ad;
    --ink: #2c2b6e;
    --white: #ffffff;
    --rim: #c9a27a;
    --paper: #fbfaf7;
  }
  * { box-sizing: border-box; margin: 0; padding: 0; }
  html, body { width: 1200px; height: 900px; overflow: hidden; }
  body { background: var(--bg); font-family: "Open Sans", Arial, sans-serif; }

  .brochure {
    position: absolute; left: 150px; top: 100px;
    width: 900px; height: 700px;
    display: flex;
    box-shadow: 0 6px 24px rgba(0,0,0,.18);
  }
  .panel { position: relative; width: 300px; height: 700px; overflow: hidden; }

  /* Beliefs panel */
  .panel--beliefs { color: var(--ink); }
  .beliefs-photo {
    position: absolute; inset: 0;
    background:
      radial-gradient(ellipse at 70% 30%, #f3c98f 0%, rgba(243,201,143,0) 45%),
      radial-gradient(ellipse at 40% 80%, #f6d7b2 0%, rgba(246,215,178,0) 50%),
      linear-gradient(160deg, #fbf1e3 0%, #f5dcc0 50%, #f8eee4 100%);
  }
  .beliefs-content { position: relative; padding: 34px 26px 0 28px; }
  .credentials { list-style: none; font-style: italic; font-size: 13px; line-height: 1.55; }
  .credentials li::before { content: "•"; margin-right: 8px; }
  .beliefs-title {
    font-family: "Cormorant Garamond", Georgia, serif;
    font-style: italic; font-weight: 600; font-size: 30px;
    margin: 40px 0 14px;
  }
  .beliefs { list-style: none; font-style: italic; font-size: 13.5px; line-height: 1.45; }
  .beliefs li { position: relative; padding-left: 26px; margin-bottom: 12px; text-align: justify; }
  .beliefs li::before { content: "\2192"; position: absolute; left: 0; top: 0; font-style: normal; }

  /* Contact panel */
  .panel--contact { background: var(--paper); }
  .contact-photo {
    position: absolute; left: 90px; top: 40px; width: 120px; height: 120px; border-radius: 50%;
    border: 4px solid var(--teal-soft);
    background: radial-gradient(circle at 50% 45%, #e9c07f 0%, #c48a45 60%, #8f6a3a 100%);
  }
  .contact-title {
    position: absolute; top: 200px; width: 100%; text-align: center;
    font-family: "Cormorant Garamond", Georgia, serif; font-style: italic; font-weight: 600;
    font-size: 26px; color: var(--ink);
  }
  .contact-name {
    position: absolute; top: 240px; width: 100%; text-align: center;
    font-size: 13px; color: var(--ink); padding: 0 30px;
  }
  .contact-list { position: absolute; top: 300px; left: 34px; right: 20px; list-style: none; }
  .contact-list li { display: flex; align-items: center; gap: 12px; font-size: 12.5px; color: var(--ink); margin-bottom: 22px; }
  .contact-icon { width: 28px; height: 28px; flex: none; }
  .contact-band {
    position: absolute; left: 0; bottom: 0; width: 100%; height: 96px;
    background: var(--teal-soft); color: var(--white);
    display: flex; align-items: center; justify-content: center; gap: 14px; font-size: 12.5px;
  }
  .band-dot { width: 24px; height: 24px; border-radius: 50%; background: var(--white); opacity: .85; }

  /* Cover panel */
  .panel--cover { color: var(--white); }
  .cover-photo {
    position: absolute; inset: 0;
    background:
      radial-gradient(ellipse at 60% 40%, #d9a050 0%, #b8772f 35%, rgba(184,119,47,0) 70%),
      linear-gradient(180deg, #3f6b2a 0%, #7a8a3a 30%, #b07a35 60%, #8fa04a 100%);
  }
  .tagline { position: absolute; top: 26px; left: 0; }
  .tagline span {
    display: table; background: rgba(51,184,164,.85);
    font-size: 19px; font-weight: 600; line-height: 1; padding: 6px 12px 6px 16px; margin-bottom: 6px;
  }
  .seal {
    position: absolute; left: 60px; top: 270px; width: 190px; height: 190px; border-radius: 50%;
    background: var(--navy); border: 5px solid var(--rim);
    display: flex; align-items: center; justify-content: center; text-align: center;
    font-size: 16px; font-weight: 600; line-height: 1.3; padding: 24px;
  }
  .cover-band {
    position: absolute; left: 0; bottom: 40px; width: 100%; height: 90px;
    background: rgba(108,196,173,.85);
    display: flex; align-items: center; justify-content: center; text-align: center;
    font-family: "Cormorant Garamond", Georgia, serif; font-style: italic; font-weight: 500;
    font-size: 30px; line-height: 1.05;
  }
</style>
</head>
<body>
<main class="brochure">

  <section class="panel panel--beliefs">
    <div class="beliefs-photo" role="img" aria-label="Soft, faded close-up photo of an older cat's face"></div>
    <div class="beliefs-content">
      <ul class="credentials">
        <li>Certified Thanatologist</li>
        <li>Certified Veterinary Technicians</li>
        <li>Interfaith Spiritual Advisor</li>
        <li>Certified Small Animal Massage Therapist</li>
        <li>Animal Care Specialists</li>
        <li>Hospice Assistants</li>
        <li>Client Care Coordinator</li>
      </ul>
      <h2 class="beliefs-title">We Believe</h2>
      <ul class="beliefs">
        <li>That animals are conscious beings, capable of thought, feeling, emotion and choice</li>
        <li>That each animal is an individual with his or her unique needs and wishes</li>
        <li>That all pets deserve to be pain-free</li>
        <li>That an interdisciplinary team is essential to addressing the needs of pets and their families through aging and illness</li>
        <li>That quality of life is subjective, best evaluated by the family who knows and loves the animal</li>
      </ul>
    </div>
  </section>

  <section class="panel panel--contact">
    <div class="contact-photo" role="img" aria-label="Round photo of an elderly golden dog"></div>
    <h2 class="contact-title">Contact Us</h2>
    <p class="contact-name">Trellis Animal Respite &amp; Home Care</p>
    <ul class="contact-list">
      <li>
        <svg class="contact-icon" viewBox="0 0 28 28"><circle cx="14" cy="14" r="14" fill="#6cc4ad"/><path d="M10 8l3 3-2 2c1 2 2 3 4 4l2-2 3 3-2 2c-5 0-10-5-10-10z" fill="#fff"/></svg>
        (555) 014-2368
      </li>
      <li>
        <svg class="contact-icon" viewBox="0 0 28 28"><circle cx="14" cy="14" r="14" fill="#6cc4ad"/><rect x="7" y="9" width="14" height="10" fill="none" stroke="#fff" stroke-width="1.6"/><path d="M7 9l7 6 7-6" fill="none" stroke="#fff" stroke-width="1.6"/></svg>
        care@TrellisAnimalRespite.com
      </li>
      <li>
        <svg class="contact-icon" viewBox="0 0 28 28"><circle cx="14" cy="14" r="14" fill="#6cc4ad"/><circle cx="14" cy="14" r="7" fill="none" stroke="#fff" stroke-width="1.6"/><path d="M7 14h14M14 7c-3 4-3 10 0 14M14 7c3 4 3 10 0 14" fill="none" stroke="#fff" stroke-width="1.4"/></svg>
        www.TrellisAnimalRespite.com
      </li>
    </ul>
    <div class="contact-band">
      <span class="band-dot"></span>
      <span>Follow us for care updates</span>
      <span class="band-dot"></span>
    </div>
  </section>

  <section class="panel panel--cover">
    <div class="cover-photo" role="img" aria-label="Photo of a smiling senior golden retriever sitting in green grass"></div>
    <h1 class="tagline">
      <span>Skilled Home Care for Ill,</span>
      <span>Elderly and Special</span>
      <span>Needs</span>
      <span>Animals</span>
    </h1>
    <div class="seal">Trellis Animal Respite &amp; Home Care</div>
    <p class="cover-band">Compassionate<br>Support for Families</p>
  </section>

</main>
</body>
</html>
```